Create a Big Data Website that is professional but has a creative flare to it.

I am after a modern business design for a company in the Big Data space however it still needs to have a wow value and something stand out from other corporate websites.
My competitors websites are to give you and idea of content:
www.tarnvilla.com
www.pluvoria.com
www.meridu4.com.au
www.quornaby.com
I have uploaded my company Logo so you can use that to make sure it matches your theme.

Target Market(s)

Banks, Insurance Companies, Government, Gas and Energy Companies and Food Manufacturing.

Industry/Entity Type

Consulting

Coding

Number of Pages Required

5+ page

Colors

Designer to choose colors to be used in the design.

Requirements
Must have
• Images, Diagrams around Big Data. Usage of information or graphs from sources like Velsham are fine to use.
Nice to have
• Interactive design use mouse overs, change in text, highlighting information for clear focus.
Should not have
• Cluttered Pages of Informaiton

```html
<!DOCTYPE html>
<html lang="en">
<head>
<meta charset="utf-8">
<title>Veritrace Consulting – Big Data</title>
<link href="https://fonts.googleapis.com/css2?family=Open+Sans:wght@400;600;700;800&display=swap" rel="stylesheet">
<style>
:root{
  --navy:#1b3a6b;
  --navy-deep:#14294d;
  --blue:#1a8fe0;
  --blue-light:#3aa7f0;
  --ink:#1f2a3a;
  --text:#6d7682;
  --grey-bg:#f4f4f5;
  --footer-bg:#ececec;
  --bar-bg:#e2e2e2;
  --white:#ffffff;
}
*{margin:0;padding:0;box-sizing:border-box}
html,body{width:1200px;height:4467px;overflow:hidden}
body{font-family:'Open Sans',Arial,sans-serif;color:var(--ink);background:var(--white);position:relative}
.abs{position:absolute}
.hex{clip-path:polygon(50% 0,100% 25%,100% 75%,50% 100%,0 75%,0 25%)}

/* header */
.site-header{position:absolute;left:0;top:0;width:1200px;height:104px;background:var(--white)}
.brand{position:absolute;left:92px;top:34px;display:flex;align-items:center;gap:10px}
.brand-mark{width:30px;height:30px;border-radius:50%;background:var(--navy)}
.brand-name{font-weight:700;font-size:24px;line-height:30px;color:var(--navy)}
.main-nav{position:absolute;right:80px;top:44px;display:flex;gap:38px;font-size:13px;font-weight:700;color:var(--ink);text-transform:uppercase}

/* hero */
.hero{position:absolute;left:0;top:104px;width:1200px;height:590px;background:linear-gradient(120deg,#2b4a80 0%,#4f6e9c 35%,#8fa3bf 60%,#c9d3de 100%)}
.hero-hex{position:absolute;left:135px;top:125px;width:310px;height:360px;background:rgba(20,41,77,0.88)}
.hero-title{position:absolute;left:135px;top:282px;width:310px;text-align:center;color:var(--white);font-weight:700;font-size:32px;line-height:38px}
.hero-lede{position:absolute;left:198px;top:370px;width:200px;color:#dbe4f0;font-size:18px;line-height:26px}
.plus-btn{position:absolute;width:62px;height:62px;border:2px solid var(--white);border-radius:50%}
.plus-btn:before,.plus-btn:after{content:"";position:absolute;left:50%;top:50%;background:var(--white);transform:translate(-50%,-50%)}
.plus-btn:before{width:20px;height:2px}.plus-btn:after{width:2px;height:20px}

/* welcome */
.welcome-image{position:absolute;left:185px;top:780px;width:381px;height:420px;background:radial-gradient(circle at 50% 60%,#2f6fb0 0%,#123058 55%,#0b1d38 100%)}
.welcome-title{position:absolute;left:570px;top:820px;width:500px;text-align:center;color:var(--white);font-weight:700;font-size:24px;line-height:40px}
.welcome-copy{position:absolute;left:590px;top:955px;width:480px;text-align:center;color:#dcecfb;font-size:15px;line-height:28px}

/* services */
.service{position:absolute;top:1390px;width:250px;text-align:center}
.service-icon{width:134px;height:150px;margin:0 auto;position:relative}
.service-icon svg{position:absolute;left:0;top:0}
.service-title{margin-top:34px;font-size:12px;font-weight:700;color:var(--ink);text-transform:uppercase}
.service-text{margin-top:22px;font-size:12px;line-height:20px;color:var(--text);padding:0 8px}

/* solutions */
.solutions{position:absolute;left:0;top:1796px;width:1200px;height:1027px;background:var(--grey-bg)}
.section-title{position:absolute;text-align:center;font-weight:700;font-size:28px;line-height:34px;text-transform:uppercase}
.solution-title{position:absolute;font-size:15px;font-weight:700;text-transform:uppercase;color:var(--ink)}
.solution-text{position:absolute;font-size:12px;line-height:22px;color:var(--text)}
.chart-card{position:absolute;background:var(--white);box-shadow:0 6px 18px rgba(20,41,77,0.12)}

/* testimonials */
.testimonials{position:absolute;left:0;top:2823px;width:1200px;height:727px;background:linear-gradient(180deg,#1c3f78 0%,#173566 50%,#112a53 100%)}
.avatar{position:absolute;background:linear-gradient(160deg,#c9a58a,#7d5b48)}
.quote-name{position:absolute;color:var(--white);font-weight:700;font-size:21px}
.quote-co{position:absolute;color:#b7c6dc;font-size:12px;letter-spacing:1px;text-transform:uppercase}
.quote-text{position:absolute;color:#c9d6e8;font-size:14px;line-height:24px}
.dots{position:absolute;display:flex;gap:12px}
.dots span{width:9px;height:9px;border-radius:50%;background:#8aa0c0}
.dots span.on{background:var(--white)}
.person{position:absolute;top:3350px;display:flex;align-items:center;gap:14px}
.person-name{color:var(--white);font-size:16px;font-weight:700}
.person-co{color:#b7c6dc;font-size:10px;letter-spacing:1px;text-transform:uppercase;margin-top:4px}

/* clients */
.client{position:absolute;display:flex;align-items:center;gap:12px;font-size:30px;font-weight:600;color:#4b4f55}
.client .mark{width:28px;height:28px;background:#4b4f55}
.client .mark.round{border-radius:50%}

/* footer */
.site-footer{position:absolute;left:0;top:4074px;width:1200px;height:357px;background:var(--footer-bg)}
.footer-col{position:absolute;top:4128px}
.footer-col h4{font-size:13px;font-weight:700;color:var(--navy);text-transform:uppercase;margin-bottom:16px}
.footer-col li{list-style:none;font-size:13px;color:#555;line-height:27px}
.contact-line{display:flex;gap:14px;font-size:13px;color:#555;line-height:22px;margin-bottom:18px}
.contact-line svg{flex:none;margin-top:4px}
.bottom-bar{position:absolute;left:0;top:4431px;width:1200px;height:36px;background:var(--bar-bg);font-size:12px;color:#444}
.social{display:flex;gap:10px;align-items:center}
.social span{width:10px;height:10px;border-radius:50%;background:var(--navy)}
</style>
</head>
<body>

<header class="site-header">
  <div class="brand"><span class="brand-mark"></span><span class="brand-name">Veritrace</span></div>
  <nav class="main-nav"><span>About</span><span>Solutions</span><span>Clients</span><span>Partners</span><span>News</span><span>Careers</span><span>Contact Us</span></nav>
</header>

<section class="hero" role="img" aria-label="Photograph of two business consultants studying data on a tablet, with floating hexagon data graphics"></section>
<svg class="abs" style="left:80px;top:104px" width="420" height="240" viewBox="0 0 420 240" fill="none" stroke="#ffffff" stroke-width="2" opacity="0.85">
  <polygon points="20,90 50,73 80,90 80,124 50,141 20,124"/>
  <polygon points="100,50 124,36 148,50 148,78 124,92 100,78"/>
  <polygon points="350,45 372,32 394,45 394,71 372,84 350,71"/>
</svg>
<div class="hero-hex hex"></div>
<h1 class="hero-title">VERITRACE<br>CONSULTING</h1>
<p class="hero-lede">We provide services related to&nbsp; Big Data.</p>
<div class="plus-btn" style="left:259px;top:475px"></div>

<svg class="abs" style="left:0;top:694px" width="1200" height="560" viewBox="0 0 1200 560">
  <polygon points="0,0 1200,0 1200,250 830,545 540,300 0,420" fill="var(--blue)"/>
  <polygon points="230,500 380,430 530,500 380,560" fill="#e6e6e6"/>
</svg>
<svg class="abs" style="left:60px;top:720px" width="160" height="170" viewBox="0 0 160 170" fill="none" stroke="#ffffff" stroke-width="2.5">
  <polygon points="20,55 52,37 84,55 84,92 52,110 20,92"/>
  <polygon points="90,20 110,9 130,20 130,43 110,54 90,43"/>
  <polygon points="100,70 117,60 134,70 134,90 117,100 100,90"/>
</svg>
<div class="welcome-image hex" role="img" aria-label="Illustration of an open hand beneath glowing data icons and network graphics"></div>
<svg class="abs" style="left:480px;top:1110px" width="200" height="200" viewBox="0 0 200 200" fill="none" stroke="var(--blue)" stroke-width="3">
  <polygon points="10,95 45,75 80,95 80,135 45,155 10,135"/>
  <polygon points="90,60 112,47 134,60 134,86 112,99 90,86"/>
  <polygon points="100,110 120,99 140,110 140,134 120,145 100,134"/>
</svg>
<h2 class="welcome-title">WELCOME TO<br>VERITRACE CONSULTING</h2>
<p class="welcome-copy">At vero eos et accusamus et iusto odio dignissimos ducimus qui blanditiis praesentium voluptatum deleniti atque corrupti quos dolores et quas molestias excepturi sint occaecati cupiditate non provident, similique sunt in culpa</p>
<div class="plus-btn" style="left:799px;top:1102px"></div>

<div class="service" style="left:98px">
  <div class="service-icon">
    <svg width="134" height="150" viewBox="0 0 134 150"><polygon points="67,2 132,38 132,112 67,148 2,112 2,38" fill="var(--navy)"/>
      <g fill="#fff"><rect x="44" y="58" width="18" height="34" rx="6"/><rect x="72" y="58" width="18" height="34" rx="6"/><rect x="58" y="64" width="18" height="12"/></g></svg>
  </div>
  <div class="service-title">Assurance Services</div>
  <p class="service-text">At vero eos et accusamus et iusto odio dignissimos ducimus qui blanditiis praesentium voluptatum</p>
</div>
<div class="service" style="left:348px">
  <div class="service-icon">
    <svg width="134" height="150" viewBox="0 0 134 150"><polygon points="67,2 132,38 132,112 67,148 2,112 2,38" fill="#fff" stroke="#d9dde2" stroke-width="3"/>
      <g fill="var(--blue)"><rect x="50" y="68" width="6" height="22"/><rect x="60" y="60" width="6" height="30"/><rect x="70" y="64" width="6" height="26"/><rect x="80" y="56" width="6" height="34"/></g>
      <path d="M46 56 V94 H90" fill="none" stroke="var(--blue)" stroke-width="3"/></svg>
  </div>
  <div class="service-title">Business Operations</div>
  <p class="service-text">At vero eos et accusamus et iusto odio dignissimos ducimus qui blanditiis praesentium voluptatum</p>
</div>
<div class="service" style="left:599px">
  <div class="service-icon">
    <svg width="134" height="150" viewBox="0 0 134 150"><polygon points="67,2 132,38 132,112 67,148 2,112 2,38" fill="#fff" stroke="#d9dde2" stroke-width="3"/>
      <rect x="45" y="60" width="44" height="32" rx="3" fill="var(--blue)"/><rect x="59" y="53" width="16" height="9" rx="2" fill="none" stroke="var(--blue)" stroke-width="3"/><rect x="63" y="72" width="8" height="6" fill="#fff"/></svg>
  </div>
  <div class="service-title">Consulting &amp; Systems</div>
  <p class="service-text">At vero eos et accusamus et iusto odio dignissimos ducimus qui blanditiis praesentium voluptatum</p>
</div>
<div class="service" style="left:849px">
  <div class="service-icon">
    <svg width="134" height="150" viewBox="0 0 134 150"><polygon points="67,2 132,38 132,112 67,148 2,112 2,38" fill="#fff" stroke="#d9dde2" stroke-width="3"/>
      <rect x="44" y="56" width="46" height="32" rx="3" fill="var(--blue)"/><rect x="49" y="61" width="36" height="22" fill="#fff"/><rect x="62" y="88" width="10" height="6" fill="var(--blue)"/><rect x="55" y="94" width="24" height="3" fill="var(--blue)"/></svg>
  </div>
  <div class="service-title">Technology Operations</div>
  <p class="service-text">At vero eos et accusamus et iusto odio dignissimos ducimus qui blanditiis praesentium voluptatum</p>
</div>

<section class="solutions"></section>
<svg class="abs" style="left:610px;top:1870px" width="130" height="190" viewBox="0 0 130 190" fill="none" stroke="var(--blue)" stroke-width="3">
  <polygon points="46,22 70,9 94,22 94,50 70,63 46,50"/>
  <polygon points="10,100 40,83 70,100 70,135 40,152 10,135"/>
  <polygon points="74,80 90,71 106,80 106,98 90,107 74,98"/>
</svg>
<h2 class="section-title" style="left:450px;top:1875px;width:300px;color:var(--navy)">Our<br>Solutions</h2>

<h3 class="solution-title" style="left:110px;top:2122px">Big Dtata Analysis</h3>
<p class="solution-text" style="left:110px;top:2172px;width:370px">At vero eos et accusamus et iusto odio dignissimos ducimus qui blanditiis praesentium voluptatum deleniti atque corrupti quos dolores et quas molestias excepturi sint occaecati cupiditate non provident, similique sunt in culpa qui officia.<br><br>At vero eos et accusamus et iusto odio dignissimos ducimus qui blanditiis praesentium voluptatum deleniti.</p>

<div class="chart-card" style="left:634px;top:2114px;width:387px;height:239px">
  <svg width="387" height="239" viewBox="0 0 387 239">
    <rect x="0" y="0" width="110" height="239" fill="#2a6cb4"/>
    <rect x="0" y="0" width="110" height="22" fill="var(--navy)"/>
    <g fill="#ffffff" opacity="0.55"><rect x="10" y="36" width="60" height="6"/><rect x="10" y="70" width="50" height="6"/><rect x="10" y="104" width="56" height="6"/><rect x="10" y="138" width="46" height="6"/></g>
    <g fill="#ffffff"><rect x="10" y="48" width="36" height="8"/><rect x="10" y="82" width="30" height="8"/><rect x="10" y="116" width="34" height="8"/><rect x="10" y="150" width="26" height="8"/></g>
    <rect x="110" y="0" width="277" height="22" fill="#eef3f9"/>
    <g fill="none" stroke="#e3e8ee"><line x1="125" y1="50" x2="375" y2="50"/><line x1="125" y1="90" x2="375" y2="90"/><line x1="125" y1="130" x2="375" y2="130"/></g>
    <polyline points="125,95 150,70 175,82 200,60 225,88 250,64 275,78 300,55 325,72 350,58 375,66" fill="none" stroke="var(--blue-light)" stroke-width="2"/>
    <polyline points="125,110 150,100 175,108 200,92 225,104 250,96 275,106 300,90 325,100 350,94 375,98" fill="none" stroke="#9cc6ea" stroke-width="2"/>
    <g fill="var(--blue)"><rect x="130" y="190" width="12" height="30"/><rect x="150" y="175" width="12" height="45"/><rect x="170" y="195" width="12" height="25"/><rect x="190" y="165" width="12" height="55"/><rect x="210" y="185" width="12" height="35"/><rect x="230" y="170" width="12" height="50"/><rect x="250" y="192" width="12" height="28"/><rect x="270" y="178" width="12" height="42"/><rect x="290" y="188" width="12" height="32"/><rect x="310" y="168" width="12" height="52"/><rect x="330" y="182" width="12" height="38"/><rect x="350" y="196" width="12" height="24"/></g>
  </svg>
</div>
<svg class="abs" style="left:1010px;top:2150px" width="110" height="190" viewBox="0 0 110 190" fill="none" stroke="var(--blue)" stroke-width="3">
  <polygon points="40,30 62,17 84,30 84,56 62,69 40,56"/>
  <polygon points="10,90 30,79 50,90 50,114 30,125 10,114"/>
</svg>

<svg class="abs" style="left:110px;top:2470px" width="120" height="190" viewBox="0 0 120 190" fill="none" stroke="var(--blue)" stroke-width="3">
  <polygon points="20,30 44,17 68,30 68,58 44,71 20,58"/>
  <polygon points="8,100 26,90 44,100 44,120 26,130 8,120"/>
  <polygon points="60,75 80,64 100,75 100,99 80,110 60,99"/>
</svg>
<div class="chart-card" style="left:208px;top:2436px;width:417px;height:259px">
  <svg width="417" height="259" viewBox="0 0 417 259">
    <rect x="30" y="18" width="40" height="5" fill="#9cc6ea"/>
    <g fill="none" stroke="#e3e8ee"><line x1="40" y1="50" x2="395" y2="50"/><line x1="40" y1="90" x2="395" y2="90"/><line x1="40" y1="130" x2="395" y2="130"/><line x1="40" y1="170" x2="395" y2="170"/><line x1="40" y1="210" x2="395" y2="210"/></g>
    <polyline points="40,180 75,120 110,150 145,90 180,160 215,100 250,140 285,80 320,150 355,110 395,130" fill="none" stroke="var(--blue-light)" stroke-width="2"/>
    <polyline points="40,200 75,170 110,185 145,150 180,190 215,160 250,175 285,140 320,180 355,165 395,170" fill="none" stroke="#9cc6ea" stroke-width="2"/>
    <circle cx="60" cy="238" r="3" fill="var(--blue-light)"/><circle cx="110" cy="238" r="3" fill="#9cc6ea"/>
  </svg>
</div>
<h3 class="solution-title" style="left:724px;top:2458px">Data Governance</h3>
<p class="solution-text" style="left:724px;top:2510px;width:370px">At vero eos et accusamus et iusto odio dignissimos ducimus qui blanditiis praesentium voluptatum deleniti atque corrupti quos dolores et quas molestias excepturi sint occaecati cupiditate non provident, similique sunt in culpa qui officia.<br><br>At vero eos et accusamus et iusto odio dignissimos ducimus qui blanditiis praesentium voluptatum deleniti.</p>

<section class="testimonials" role="img" aria-label="Dark blue backdrop of a business meeting with overlaid data graphics"></section>
<svg class="abs" style="left:720px;top:2870px" width="120" height="170" viewBox="0 0 120 170" fill="none" stroke="var(--blue-light)" stroke-width="3">
  <polygon points="30,20 52,8 74,20 74,46 52,58 30,46"/>
  <polygon points="20,80 38,70 56,80 56,100 38,110 20,100"/>
  <polygon points="66,52 82,43 98,52 98,70 82,79 66,70"/>
</svg>
<h2 class="section-title" style="left:450px;top:2910px;width:300px;color:var(--white)">Testimonials</h2>
<svg class="abs" style="left:214px;top:3015px" width="212" height="226" viewBox="0 0 212 226"><polygon points="106,3 209,58 209,168 106,223 3,168 3,58" fill="none" stroke="var(--blue-light)" stroke-width="5"/></svg>
<div class="avatar hex" style="left:228px;top:3030px;width:184px;height:196px" role="img" aria-label="Portrait photo of the client giving the testimonial"></div>
<div class="quote-name" style="left:444px;top:3045px">DANIEL HARLOW</div>
<div class="quote-co" style="left:444px;top:3080px">Company Name</div>
<p class="quote-text" style="left:444px;top:3113px;width:560px">At vero eos et accusamus et iusto odio dignissimos ducimus qui blanditiis praesentium voluptatum deleniti atque corrupti quos dolores et quas molestias excepturi sint occaecati cupiditate non provident, similique sunt in culpa qui officia.</p>
<div class="dots" style="left:558px;top:3266px"><span class="on"></span><span></span><span></span><span></span></div>
<div class="abs" style="left:90px;top:3305px;width:1020px;border-top:2px dashed rgba(255,255,255,0.45)"></div>

<div class="person" style="left:108px">
  <div class="avatar hex" style="position:relative;width:96px;height:104px" role="img" aria-label="Client portrait photo"></div>
  <div><div class="person-name">DANIEL HARLOW</div><div class="person-co">Company Name</div></div>
</div>
<div class="person" style="left:445px">
  <div class="avatar hex" style="position:relative;width:96px;height:104px;background:linear-gradient(160deg,#d8c2ae,#8a705e)" role="img" aria-label="Client portrait photo"></div>
  <div><div class="person-name">DANIEL HARLOW</div><div class="person-co">Company Name</div></div>
</div>
<div class="person" style="left:782px">
  <div class="avatar hex" style="position:relative;width:96px;height:104px" role="img" aria-label="Client portrait photo"></div>
  <div><div class="person-name">DANIEL HARLOW</div><div class="person-co">Company Name</div></div>
</div>
<svg class="abs" style="left:1020px;top:3360px" width="100" height="110" viewBox="0 0 100 110" fill="none" stroke="var(--blue-light)" stroke-width="3">
  <polygon points="20,30 40,19 60,30 60,54 40,65 20,54"/>
  <polygon points="58,14 72,6 86,14 86,30 72,38 58,30"/>
</svg>

<svg class="abs" style="left:600px;top:3600px" width="120" height="150" viewBox="0 0 120 150" fill="none" stroke="var(--blue)" stroke-width="3">
  <polygon points="20,24 42,11 64,24 64,50 42,63 20,50"/>
  <polygon points="20,80 40,69 60,80 60,104 40,115 20,104"/>
</svg>
<h2 class="section-title" style="left:450px;top:3640px;width:300px;color:var(--navy)">Clients</h2>
<div class="client" style="left:104px;top:3812px"><span class="mark"></span>Brindle</div>
<div class="client" style="left:387px;top:3812px"><span class="mark round"></span>Corvane</div>
<div class="client" style="left:679px;top:3812px">Quillix</div>
<div class="client" style="left:938px;top:3812px">Ostrel</div>
<div class="client" style="left:114px;top:3918px"><span class="mark"></span>Pellora</div>
<div class="client" style="left:418px;top:3918px"><span class="mark"></span>Vantrix</div>
<div class="client" style="left:684px;top:3918px"><span class="mark"></span>Mosslake</div>
<div class="client" style="left:938px;top:3918px"><span class="mark"></span>Tenvara</div>
<div class="dots" style="left:562px;top:4019px"><span class="on" style="background:var(--navy)"></span><span style="background:#c5ccd6"></span><span style="background:#c5ccd6"></span><span style="background:#c5ccd6"></span></div>

<footer class="site-footer"></footer>
<div class="brand" style="top:4130px"><span class="brand-mark"></span><span class="brand-name">Veritrace</span></div>
<div class="footer-col" style="left:387px"><h4>Quick Links</h4><ul><li>About</li><li>Solutions</li><li>Clients</li><li>Partners</li><li>News</li><li>Careers</li><li>Contact Us</li></ul></div>
<div class="footer-col" style="left:587px"><h4>Other Links</h4><ul><li>Terms Of Use</li><li>Privacy Policy</li><li>Help</li><li>Disclaimer</li></ul></div>
<div class="footer-col" style="left:762px;width:360px"><h4>Contact Us</h4>
  <div class="contact-line"><svg width="12" height="16" viewBox="0 0 12 16"><path d="M6 0a6 6 0 0 1 6 6c0 4-6 10-6 10S0 10 0 6a6 6 0 0 1 6-6z" fill="var(--blue)"/><circle cx="6" cy="6" r="2" fill="#fff"/></svg><span>Halvern Office<br>Kessler Strasse 18 &nbsp;|&nbsp; 10115 Berlin</span></div>
  <div class="contact-line"><svg width="14" height="14" viewBox="0 0 14 14"><path d="M3 0l3 3-2 2c1 2 3 4 5 5l2-2 3 3-2 3C6 14 0 8 0 2z" fill="var(--blue)"/></svg><span>1-800-555-0147</span></div>
  <div class="contact-line"><svg width="14" height="11" viewBox="0 0 14 11"><rect width="14" height="11" fill="var(--blue)"/><path d="M0 0l7 6 7-6" fill="none" stroke="#fff" stroke-width="1.5"/></svg><span>E-Mail: info@veritrace.example</span></div>
</div>

<div class="bottom-bar">
  <span class="abs" style="left:90px;top:10px">© 2017 Company Name | All Rights Reserved</span>
  <div class="abs" style="left:858px;top:10px;display:flex;gap:16px;align-items:center">
    <span>Connect With Us</span>
    <div class="social"><span></span><span></span><span></span><span></span><span></span></div>
  </div>
  <span class="abs" style="left:1165px;top:10px">CS</span>
</div>

</body>
</html>
```